Website Design Project for Beauty & Wellness Professionals

As background information, I have a website that is focused on Beauty & Wellness Professionals:
- Job Search (www.lumarinovo.com)
- Business Classifieds (negocios.lumarinovo.com)
- Freelancer Classifieds (freelancer.lumarinovo.com)
- Course Reviews (cursos.lumarinovo.com)

All those websites use standard templates.

I need a DESIGN for the HOME PAGE (no coding) of the Website Platform that consolidates the four platforms under the same design.

Website designs that we like:
- quelvox.com
- brintmoor.com

Target Market(s)

Brazilian Professionals from Beauty & Wellness sector

Industry/Entity Type

Business

Requirements
Must have
• Website designs that we like:
- quelvox.com
- brintmoor.com

```html
<!DOCTYPE html>
<html lang="en">
<head>
<meta charset="utf-8">
<title>Lumarinovo – Beauty &amp; Wellness Jobs</title>
<link href="https://fonts.googleapis.com/css2?family=Open+Sans:wght@400;600;700&display=swap" rel="stylesheet">
<style>
:root{
  --green:#62ad2c;
  --green-dark:#3f8a1c;
  --green-light:#8cc63f;
  --blue:#2a84b4;
  --blue-dark:#1f6d96;
  --page:#e8e9e9;
  --panel:#ffffff;
  --line:#e1e3e3;
  --text:#555b5e;
  --muted:#8b9194;
  --orange:#f07d1e;
  --red:#d9412f;
  --net-blue:#3b5a98;
  --net-sky:#35b3e4;
}
*{box-sizing:border-box;margin:0;padding:0}
html,body{width:1200px;height:2948px;overflow:hidden}
body{background:var(--page);font-family:"Open Sans",Arial,sans-serif;color:var(--text);font-size:13px;position:relative}
a{color:inherit;text-decoration:none}

.topbar{position:absolute;left:0;top:0;width:1200px;height:152px;background:#fff}
.brand{position:absolute;left:130px;top:40px;display:flex;align-items:center;gap:12px;color:var(--green);font-size:34px;font-weight:600}
.brand-dot{width:22px;height:22px;border-radius:50%;background:var(--green)}
.account-links{position:absolute;right:130px;top:10px;font-size:13px;color:var(--muted)}
.account-links span{margin:0 6px}

.main-nav{position:absolute;left:0;top:152px;width:1200px;height:34px;background:linear-gradient(#6fb935,#579f24)}
.main-nav ul{list-style:none;display:flex;margin-left:150px;height:34px;align-items:center}
.main-nav li{color:#fff;font-size:14px;font-weight:600;padding:0 20px}
.main-nav li:first-child{background:var(--green-dark);height:34px;line-height:34px}

.hero{position:absolute;left:0;top:186px;width:1200px;height:450px;background:linear-gradient(100deg,#dcd4c7 0%,#c9b6a0 30%,#e6ddd2 55%,#f4efe8 75%,#cfe3c4 100%)}
.hero-dots{position:absolute;left:566px;top:612px;display:flex;gap:6px}
.hero-dots i{width:10px;height:10px;border-radius:50%;background:#fff;opacity:.7}
.hero-dots i:first-child{background:#333;opacity:1}

.search-tabs{position:absolute;left:160px;top:412px;display:flex;gap:4px}
.search-tabs span{background:var(--blue);color:#fff;font-size:12px;font-weight:600;padding:5px 22px}
.search-tabs span+span{background:var(--green)}
.search-panel{position:absolute;left:160px;top:438px;width:880px;height:160px;background:rgba(255,255,255,.92);padding:20px 30px}
.search-grid{display:grid;grid-template-columns:1fr 1fr;gap:14px 30px}
.field{height:28px;border:1px solid #cfd3d4;background:#fff;font-size:11px;color:var(--muted);padding:6px 10px;position:relative}
.field::after{content:"";position:absolute;right:10px;top:11px;border:5px solid transparent;border-top-color:#888}
.search-btn{position:absolute;right:30px;bottom:16px;background:var(--blue);color:#fff;font-size:13px;font-weight:600;padding:6px 26px}

.content{position:absolute;left:120px;top:660px;width:960px;height:2160px;background:var(--panel);box-shadow:0 0 4px rgba(0,0,0,.08)}
.jobs{position:absolute;left:22px;top:0;width:610px}
.section-title{color:var(--blue);font-size:19px;font-weight:600;border-bottom:1px solid var(--line);padding-bottom:8px}
.featured{position:absolute;top:26px;left:0;width:610px}
.latest{position:absolute;top:910px;left:0;width:610px}
.job{display:flex;gap:18px;border-bottom:1px solid var(--line);padding:14px 0 0}
.featured .job{height:152px}
.latest .job{height:180px}
.job-side{width:82px;flex:none}
.thumb{width:82px;height:74px;border:1px solid var(--line)}
.job-date{font-size:10px;color:var(--green-dark);text-align:center;margin-top:6px}
.job-badge{display:inline-block;margin-top:10px;background:var(--green);color:#fff;font-size:9px;font-weight:600;padding:3px 6px}
.job-badge.alt{background:var(--orange)}
.job-body{flex:1}
.job-title{color:var(--blue);font-size:16px}
.job-meta{font-size:11px;line-height:16px;margin-top:6px}
.job-place{font-size:11px;margin-top:22px;color:var(--muted)}
.pager{position:absolute;top:842px;right:0;display:flex;gap:6px}
.pager span{border:1px solid #cfd3d4;font-size:10px;padding:3px 8px;color:var(--muted)}

.sidebar{position:absolute;left:672px;top:40px;width:268px}
.sidebar h3{color:var(--blue);font-size:16px;font-weight:600;margin-bottom:8px}
.search-box{background:var(--green);padding:10px 12px;height:190px;color:#fff}
.search-box h3{color:#fff;margin-bottom:10px}
.search-box .input{height:24px;background:#fff;border:1px solid #c6d9b6}
.search-box .go{display:inline-block;background:var(--green-dark);font-size:10px;padding:3px 10px;margin-top:8px}
.search-box p{font-size:10px;margin-top:10px;line-height:14px}
.cat-list{list-style:none}
.cat-list li{font-size:12px;height:30px;line-height:30px;border-bottom:1px solid var(--line);padding-left:20px;position:relative}
.cat-list li::before{content:"";position:absolute;left:4px;top:12px;width:7px;height:7px;background:var(--green)}
.ad-banner{margin-top:14px;height:220px;background:linear-gradient(135deg,#1a1a1a 0%,#3d1012 45%,#d8331f 80%,#f29a2e 100%)}
.course{margin-top:20px}
.course-img{height:110px;background:linear-gradient(120deg,#40255c,#8a5aa6 60%,#c9a7dc)}
.course p{font-size:11px;line-height:16px;margin-top:8px}
.btn-small{display:inline-block;background:var(--orange);color:#fff;font-size:10px;padding:3px 10px;margin-top:6px}
.newsletter{margin-top:22px}
.newsletter p{font-size:11px;line-height:16px}
.newsletter .input{height:26px;border:1px solid #cfd3d4;margin-top:8px}
.newsletter .btn-small{background:var(--green)}
.connect{margin-top:30px;border-top:1px solid var(--line);padding-top:12px}
.social{display:flex;justify-content:space-between;align-items:center;height:60px;border-bottom:1px solid var(--line)}
.social strong{font-size:12px;font-weight:600;display:block}
.social small{font-size:10px;color:var(--muted)}
.social i{width:30px;height:30px;border-radius:50%;flex:none}

.site-footer{position:absolute;left:120px;top:2852px;width:960px;font-size:12px;color:var(--muted)}
.site-footer nav span{margin-right:8px}
.site-footer p{margin-top:14px;font-size:11px}
</style>
</head>
<body>

<header class="topbar">
  <a class="brand" href="#"><span class="brand-dot"></span>Lumarinovo</a>
  <div class="account-links">Advertise Job Vacancy<span>|</span>Login<span>|</span>Register</div>
</header>

<nav class="main-nav">
  <ul>
    <li>Home</li><li>Blog</li><li>For Professionals</li><li>For Business</li><li>Events &amp; Partners</li><li>About U.S</li><li>Testimonials</li><li>Contact Us</li>
  </ul>
</nav>

<section class="hero" role="img" aria-label="Woman relaxing during a spa facial massage"></section>
<div class="search-tabs"><span>Search By</span><span>Type</span></div>
<form class="search-panel">
  <div class="search-grid">
    <div class="field">Job Type</div><div class="field">Location</div>
    <div class="field">Job Category</div><div class="field">Posted Date</div>
  </div>
  <span class="search-btn">Search</span>
</form>
<div class="hero-dots"><i></i><i></i><i></i><i></i></div>

<main class="content">
  <div class="jobs">
    <section class="featured">
      <h2 class="section-title">Featured Job Vacancies</h2>
      <article class="job"><div class="job-side"><div class="thumb" role="img" aria-label="Salon logo" style="background:linear-gradient(#f4f4f4,#d9d9d9)"></div><div class="job-date">July 18,2013</div><span class="job-badge">Registered 2/11</span></div><div class="job-body"><div class="job-title">Aux. Hairdresser (Escovista) - Santo André (SP)</div><div class="job-meta">Marina Teles / Salão Orvalho - Posted by<br>Marina Teles</div><div class="job-place">Santo André São Paulo, the Federative Republic of Brazil</div></div></article>
      <article class="job"><div class="job-side"><div class="thumb" role="img" aria-label="Salon logo" style="background:linear-gradient(#2b2b2b,#111)"></div><div class="job-date">July 18,2013</div><span class="job-badge">Registered 2/11</span></div><div class="job-body"><div class="job-title">Aux. Hairdresser (Escovista) - Santo André (SP)</div><div class="job-meta">Marina Teles / Salão Orvalho - Posted by<br>Marina Teles</div><div class="job-place">Santo André São Paulo, the Federative Republic of Brazil</div></div></article>
      <article class="job"><div class="job-side"><div class="thumb" role="img" aria-label="Salon logo" style="background:linear-gradient(#eef5e6,#b8d79a)"></div><div class="job-date">July 18,2013</div><span class="job-badge">Registered 2/11</span></div><div class="job-body"><div class="job-title">Aux. Hairdresser (Escovista) - Santo André (SP)</div><div class="job-meta">Marina Teles / Salão Orvalho - Posted by<br>Marina Teles</div><div class="job-place">Santo André São Paulo, the Federative Republic of Brazil</div></div></article>
      <article class="job"><div class="job-side"><div class="thumb" role="img" aria-label="Salon logo" style="background:linear-gradient(#fafafa,#e4e4e4)"></div><div class="job-date">July 18,2013</div><span class="job-badge">Registered 2/11</span></div><div class="job-body"><div class="job-title">Aux. Hairdresser (Escovista) - Santo André (SP)</div><div class="job-meta">Marina Teles / Salão Orvalho - Posted by<br>Marina Teles</div><div class="job-place">Santo André São Paulo, the Federative Republic of Brazil</div></div></article>
      <article class="job"><div class="job-side"><div class="thumb" role="img" aria-label="Salon logo" style="background:linear-gradient(#f1f6ea,#c6dcac)"></div><div class="job-date">July 18,2013</div><span class="job-badge">Registered 2/11</span></div><div class="job-body"><div class="job-title">Aux. Hairdresser (Escovista) - Santo André (SP)</div><div class="job-meta">Marina Teles / Salão Orvalho - Posted by<br>Marina Teles</div><div class="job-place">Santo André São Paulo, the Federative Republic of Brazil</div></div></article>
    </section>
    <div class="pager"><span>Prev</span><span>1</span><span>2</span><span>3</span><span>4</span><span>5</span><span>6</span><span>...</span><span>10</span><span>Next</span></div>

    <section class="latest">
      <h2 class="section-title">Latest Job Vacancies</h2>
      <article class="job"><div class="job-side"><div class="thumb" role="img" aria-label="Salon logo" style="background:linear-gradient(#f3ece2,#d7c3a8)"></div><div class="job-date">July 18,2013</div><span class="job-badge">Registered 2/11</span></div><div class="job-body"><div class="job-title">Aux. Hairdresser (Escovista) - Santo André (SP)</div><div class="job-meta">Marina Teles / Salão Orvalho - Posted by<br>Marina Teles</div><div class="job-place">Santo André São Paulo, the Federative Republic of Brazil</div></div></article>
      <article class="job"><div class="job-side"><div class="thumb" role="img" aria-label="Salon logo" style="background:linear-gradient(#fbe3c2,#f0a24a)"></div><div class="job-date">July 18,2013</div><span class="job-badge alt">Registered 2/11</span></div><div class="job-body"><div class="job-title">Aux. Hairdresser (Escovista) - Santo André (SP)</div><div class="job-meta">Marina Teles / Salão Orvalho - Posted by<br>Marina Teles</div><div class="job-place">Santo André São Paulo, the Federative Republic of Brazil</div></div></article>
      <article class="job"><div class="job-side"><div class="thumb" role="img" aria-label="Salon logo" style="background:linear-gradient(#e8e2dc,#a99384)"></div><div class="job-date">July 18,2013</div><span class="job-badge">Registered 2/11</span></div><div class="job-body"><div class="job-title">Aux. Hairdresser (Escovista) - Santo André (SP)</div><div class="job-meta">Marina Teles / Salão Orvalho - Posted by<br>Marina Teles</div><div class="job-place">Santo André São Paulo, the Federative Republic of Brazil</div></div></article>
      <article class="job"><div class="job-side"><div class="thumb" role="img" aria-label="Salon logo" style="background:linear-gradient(#f1f6ea,#b7d490)"></div><div class="job-date">July 18,2013</div><span class="job-badge">Registered 2/11</span></div><div class="job-body"><div class="job-title">Aux. Hairdresser (Escovista) - Santo André (SP)</div><div class="job-meta">Marina Teles / Salão Orvalho - Posted by<br>Marina Teles</div><div class="job-place">Santo André São Paulo, the Federative Republic of Brazil</div></div></article>
      <article class="job"><div class="job-side"><div class="thumb" role="img" aria-label="Salon logo" style="background:linear-gradient(#f1f6ea,#b7d490)"></div><div class="job-date">July 18,2013</div><span class="job-badge">Registered 2/11</span></div><div class="job-body"><div class="job-title">Aux. Hairdresser (Escovista) - Santo André (SP)</div><div class="job-meta">Marina Teles / Salão Orvalho - Posted by<br>Marina Teles</div><div class="job-place">Santo André São Paulo, the Federative Republic of Brazil</div></div></article>
      <article class="job"><div class="job-side"><div class="thumb" role="img" aria-label="Salon logo" style="background:linear-gradient(#f1f6ea,#b7d490)"></div><div class="job-date">July 18,2013</div><span class="job-badge">Registered 2/11</span></div><div class="job-body"><div class="job-title">Aux. Hairdresser (Escovista) - Santo André (SP)</div><div class="job-meta">Marina Teles / Salão Orvalho - Posted by<br>Marina Teles</div><div class="job-place">Santo André São Paulo, the Federative Republic of Brazil</div></div></article>
    </section>
  </div>

  <aside class="sidebar">
    <div class="search-box">
      <h3>Search Your Job</h3>
      <div class="input"></div>
      <span class="go">Search Now</span>
      <p>Ex: Hairdresser São Paulo, Esthetician or Assistant Hairdresser</p>
    </div>

    <h3 style="margin-top:28px">Job Vacancies</h3>
    <ul class="cat-list">
      <li>Assistant Hairdresser</li><li>Assistant Cleaning</li><li>Hairdresser</li><li>Esthetic</li><li>Designer Eyebrows</li><li>Featured</li><li>Nurse</li><li>Beautician</li><li>Physiotherapist</li><li>Management / Coordination</li><li>Manicure and Pedicure</li><li>Makeup artist</li><li>Massage therapist</li><li>Other</li><li>Podiatrist</li><li>Reception / Customer</li><li>Cosmetics sales</li>
    </ul>

    <div class="ad-banner" role="img" aria-label="Advertising banner of an athlete jumping with sports promotion"></div>

    <div class="course">
      <h3>Online Course Tavora</h3>
      <div class="course-img" role="img" aria-label="Online makeup course cover"></div>
      <p>Lorem ipsum is simply dummy text of the printing and typesetting industry. Lorem Ipsum has been the industry's standard dummy text ever since the 1500s, when an unknown.</p>
      <span class="btn-small">Read More</span>
    </div>

    <div class="newsletter">
      <h3>Sign Up Newsletter</h3>
      <p>Lorem ipsum is simply dummy text of the printing and typesetting</p>
      <div class="input"></div>
      <span class="btn-small">Subscribe</span>
    </div>

    <div class="connect">
      <h3>Connect With Us</h3>
      <div class="social"><div><strong>Subscribe</strong><small>Receive the latest jobs</small></div><i style="background:var(--orange)"></i></div>
      <div class="social"><div><strong>Follow Us</strong><small>Come join us on Chirplo</small></div><i style="background:var(--net-sky)"></i></div>
      <div class="social"><div><strong>Follow us</strong><small>Come join us on Vistago</small></div><i style="background:var(--red)"></i></div>
      <div class="social"><div><strong>Take part!</strong><small>Be part of our network on Frendora</small></div><i style="background:var(--net-blue)"></i></div>
    </div>
  </aside>
</main>

<footer class="site-footer">
  <nav><span>Home</span>|<span> Blog</span>|<span> For Professionals</span>|<span> For Business</span>|<span> Events &amp; Partners</span>|<span> About U.S</span>|<span> Testimonials</span>|<span> Contact Us</span></nav>
  <p>© 2013 Lumarinovo. All Rights Reserved</p>
</footer>

</body>
</html>
```